Create website for home automation - Control your lighting, fans, blinds etc remotely by smartphone

Plan for SHOPIFY Website - Our Clever Dwelling
Company name: Our Clever Dwelling
Company Slogan: Calm Evenings Come Naturally
Clean, Modern, Easy to Navigate, easy to maintain - not a lot of coding. We need flash technology but displaying simply what we do.
What we provide:
We will be offering wireless switch which can be added to iOS/Android App via WiFi, allowing users to remotely turn on/off connected lights, fans, security cameras, appliances, irrigation, humidifier separately from anywhere at any time.
Control your home away from home. No more wandering of your mind on those lights or appliances which you might have left switched on. No need to drive back home to check and switch them off. Save that energy, money and time just with a click of your phone no matter how far you are from home.
Replace your home electrical switches with smart switches. They retrofit existing electrical switches and allow you to make the transformation as needed.
Easy to use and intuitive app allows you to control your lights and devices just at a click. Set any kind of ambiance suiting your occasion.
Set scenes in smartphone app to group and operate your devices just at a button click. Same device can be included in more than one scene.
Collections and Products
Light Switches
Wall Plugs
Fan Switch
Pendants etc special lighting types.
Light Dimmers
Blind Controllers
Home Page:
Home page needs to telling customers what we do and how we do it in a few words to grab people.
Phone
Email
Support – Download instructions per product
Client login
Wholesale login
Promotional video to be on home screen - this is a short 1.5 - 2 min illustration introduction video to who we are and what we do - this is yet to be created)
Social media link - Facebook
Pages:
FAQ
About Us
Support/Shipping/Returns policy
Support/Installation
Blog posts
Product pages:
Description
Price
Space for where a video will be featured - how each product works/installation.
Reviews
Our competition:
http://www.brivo.com.au
https://lumigardenhub.com.au/2018/04/05/best-smart-light-switches-and-plugs/
https://www.tavelinq.com

```html
<!DOCTYPE html>
<html lang="en">
<head>
<meta charset="utf-8">
<title>Our Clever Dwelling</title>
<link rel="stylesheet" href="https://fonts.googleapis.com/css2?family=Poppins:wght@400;500;600;700&display=swap">
<style>
:root{
  --blue:#1b75c4;
  --blue-dark:#0e5ea5;
  --ink:#222;
  --muted:#6b6b6b;
  --line:#dcdcdc;
  --black:#0b0b0b;
  --white:#fff;
}
*{box-sizing:border-box;margin:0;padding:0}
html,body{width:1200px;height:4144px;overflow:hidden}
body{font-family:"Poppins",sans-serif;color:var(--ink);background:var(--white);position:relative}
.abs{position:absolute}
.topbar{top:0;left:0;width:1200px;height:36px;background:var(--blue);color:var(--white);font-size:14px;display:flex;align-items:center;justify-content:center}
.header{top:36px;left:0;width:1200px;height:212px}
.social{left:96px;top:70px;display:flex;gap:12px}
.social span{width:28px;height:28px;border-radius:50%;background:var(--blue);display:block}
.brand{left:0;width:1200px;top:44px;display:flex;flex-direction:column;align-items:center;gap:8px}
.brand .mark{width:48px;height:48px;border-radius:50%;background:var(--blue)}
.brand .name{font-weight:700;font-size:20px;color:var(--blue-dark);letter-spacing:1px;text-transform:uppercase}
.tools{right:96px;top:68px;display:flex;gap:24px;align-items:center;font-size:14px;color:var(--muted)}
.nav{top:160px;left:0;width:1200px;display:flex;justify-content:center;gap:34px;font-size:15px;color:#333}
.hero{top:248px;left:0;width:1200px;height:552px;background:linear-gradient(120deg,#46525c 0%,#1e2630 45%,#3c4550 100%)}
.hero h1{position:absolute;top:236px;width:1200px;text-align:center;color:var(--white);font-size:52px;font-weight:600;line-height:64px}
.hero p{position:absolute;top:314px;width:1200px;text-align:center;color:var(--white);font-size:32px;line-height:40px}
.arrow{top:502px;width:44px;height:44px;border-radius:50%}
.section-title{left:0;width:1200px;text-align:center;color:var(--blue);font-weight:600;font-size:36px}
.lead{left:150px;width:900px;text-align:center;font-size:14px;line-height:26px;color:var(--muted)}
.card{top:1192px;width:304px;height:308px}
.card-label{color:var(--white);text-align:center;width:100%;position:absolute;top:130px;font-size:18px;font-weight:500;line-height:30px}
.video{top:1752px;left:0;width:1200px;height:516px;background:linear-gradient(110deg,#6a5a24 0%,#2d3a2a 40%,#20262c 70%,#554020 100%)}
.play{left:566px;top:224px;width:68px;height:68px;border-radius:50%}
.feature{left:0;width:1200px;height:424px;display:flex}
.feature .text{width:600px;padding:88px 96px 0 112px;color:var(--white)}
.feature h3{font-size:38px;font-weight:600;margin-bottom:22px}
.feature p{font-size:16px;line-height:24px}
.feature .media{width:600px;height:100%}
.blog{top:3208px;width:216px}
.blog .date{font-size:13px;color:var(--muted);line-height:20px}
.blog h4{font-size:14px;font-weight:600;margin-top:6px;line-height:22px;white-space:nowrap}
.blog .thumb{margin-top:16px;height:140px}
.blog p{margin-top:24px;font-size:12px;line-height:20px;color:var(--muted)}
.quote{top:3532px;left:240px;width:720px;text-align:center;font-size:18px;line-height:32px}
.byline{top:3614px;left:0;width:1200px;text-align:center;font-size:13px;color:var(--muted)}
.footer{top:3720px;left:120px;width:960px;height:300px;border-top:1px solid var(--line);display:flex}
.footer .col{padding-top:50px;text-align:center}
.footer .col+.col{border-left:1px solid var(--line)}
.footer h5{font-size:16px;font-weight:600;margin-bottom:18px}
.footer p{font-size:14px;line-height:22px;color:var(--muted)}
.foot-social{display:flex;gap:14px;justify-content:center}
.foot-social span{width:32px;height:32px;border-radius:50%;background:var(--blue-dark);display:block}
.signup{display:flex;gap:8px;justify-content:center}
.signup .field{width:160px;height:36px;border:1px solid var(--line);font-size:12px;color:var(--muted);text-align:left;padding:9px 10px}
.signup .btn{width:96px;height:36px;background:var(--blue);color:var(--white);font-size:13px;padding-top:8px}
.bottombar{top:4020px;left:0;width:1200px;height:124px;background:var(--black);color:var(--white)}
.bottombar .links{position:absolute;top:34px;width:1200px;display:flex;justify-content:center;gap:30px;font-size:14px}
.bottombar .copy{position:absolute;top:76px;width:1200px;text-align:center;font-size:13px}
.bottombar .cur{position:absolute;right:40px;top:76px;font-size:13px}
</style>
</head>
<body>
<div class="abs topbar">Sed ut perspiciatis unde omnis iste natus error sit voluptatem</div>

<header class="abs header">
  <div class="abs social"><span></span><span></span><span></span></div>
  <div class="abs brand"><span class="mark"></span><span class="name">Our Clever Dwelling</span></div>
  <div class="abs tools">
    <svg width="22" height="22" viewBox="0 0 24 24" fill="none" stroke="#444" stroke-width="2.4"><circle cx="10" cy="10" r="7"/><path d="M15 15l6 6"/></svg>
    <svg width="24" height="24" viewBox="0 0 24 24" fill="#444"><circle cx="12" cy="8" r="5"/><path d="M3 22c0-6 4-8 9-8s9 2 9 8z"/></svg>
    <span>
      <svg width="20" height="20" viewBox="0 0 24 24" fill="#444" style="vertical-align:middle"><path d="M5 8h14l-1.5 13h-11z"/><path d="M8 8a4 4 0 0 1 8 0" fill="none" stroke="#444" stroke-width="2"/></svg>
      Cart
    </span>
  </div>
  <nav class="abs nav"><span>Home</span><span>Product</span><span>FAQs</span><span>About Us</span><span>Support</span><span>Blog Posts</span><span>Contact Us</span></nav>
</header>

<section class="abs hero" role="img" aria-label="Smartphone controlling a smart home with wireless signal icons over a city at dusk">
  <h1>Our Clever Dwelling</h1>
  <p>Calm Evenings Come Naturally</p>
</section>
<svg class="abs arrow" style="left:40px" viewBox="0 0 44 44" aria-hidden="true"><circle cx="22" cy="22" r="22" fill="#fff" opacity=".9"/><path d="M25 14l-8 8 8 8" fill="none" stroke="#222" stroke-width="3"/></svg>
<svg class="abs arrow" style="right:40px" viewBox="0 0 44 44" aria-hidden="true"><circle cx="22" cy="22" r="22" fill="#fff" opacity=".9"/><path d="M19 14l8 8-8 8" fill="none" stroke="#222" stroke-width="3"/></svg>

<h2 class="abs section-title" style="top:862px">About Us</h2>
<p class="abs lead" style="top:926px">Lorem ipsum dolor sit amet, consectetur adipiscing elit, sed do eiusmod tempor incididunt ut labore et dolore magna aliqua. Ut enim ad minim veniam, quis nostrud exercitation ullamco laboris nisi ut aliquip ex ea commodo consequat. Duis aute irure dolor in reprehenderit in voluptate velit esse cillum dolore eu fugiat nulla pariatur. Excepteur sint occaecat cupidatat non proident, sunt in culpa qui officia deserunt mollit anim.</p>

<h2 class="abs section-title" style="top:1106px">Featured Products</h2>
<div class="abs card" style="left:136px;background:linear-gradient(160deg,#8d9196,#4a4e53)" role="img" aria-label="Wireless smart hub product on a grey background"></div>
<div class="abs card" style="left:448px;background:linear-gradient(160deg,#3a3c40,#141517)" role="img" aria-label="Dark smart wall panel showing product categories">
  <div class="card-label"><span style="font-size:14px">Menu</span><br>Product Categories<br><span style="font-size:14px">$249.00</span></div>
</div>
<div class="abs card" style="left:776px;background:linear-gradient(160deg,#e8e6e2,#a9a59d)" role="img" aria-label="Smart thermostat on a light wall"></div>

<h2 class="abs section-title" style="top:1568px;font-size:28px">Sed ut perspiciatis unde omnis iste natus</h2>

<section class="abs video" role="img" aria-label="Promotional video: hands holding a home control tablet">
  <svg class="abs play" viewBox="0 0 68 68" aria-hidden="true"><circle cx="34" cy="34" r="34" fill="#fff" opacity=".92"/><path d="M27 21l22 13-22 13z" fill="#222"/></svg>
</section>

<section class="abs feature" style="top:2268px">
  <div class="text" style="background:var(--blue)">
    <h3>Product Name</h3>
    <p>Lorem ipsum dolor sit amet, consectetur adipiscing elit, sed do eiusmod tempor incididunt ut labore et dolore magna aliqua. Ut enim ad minim veniam, quis nostrud exercitation ullamco laboris nisi ut aliquip ex ea commodo consequat. Duis aute irure dolor in reprehenderit in voluptate velit esse cillum dolore eu fugiat nulla pariatur.</p>
  </div>
  <div class="media" style="background:linear-gradient(135deg,#2b2b2b,#6d6d6d 60%,#1d1d1d)" role="img" aria-label="Hand holding a phone beside a smart door lock"></div>
</section>

<section class="abs feature" style="top:2692px">
  <div class="media" style="background:linear-gradient(120deg,#cfd3d6,#8b7a66 60%,#4c4036)" role="img" aria-label="Smart wall panel in a bright living room"></div>
  <div class="text" style="background:var(--black)">
    <h3>Product Name</h3>
    <p>Lorem ipsum dolor sit amet, consectetur adipiscing elit, sed do eiusmod tempor incididunt ut labore et dolore magna aliqua. Ut enim ad minim veniam, quis nostrud exercitation ullamco laboris nisi ut aliquip ex ea commodo consequat. Duis aute irure dolor in reprehenderit in voluptate velit esse cillum dolore eu fugiat nulla pariatur.</p>
  </div>
</section>

<article class="abs blog" style="left:120px"><div class="date">Oct 10, 2018</div><h4>Lorem ipsum dolor sit amet</h4><div class="thumb" style="background:linear-gradient(135deg,#bcd6ea,#4f86b4)" role="img" aria-label="Phone showing a smart home app"></div><p>Sed ut perspiciatis unde omnis iste natus error sit voluptatem accusantium doloremque.</p></article>
<article class="abs blog" style="left:360px"><div class="date">Oct 10, 2018</div><h4>Lorem ipsum dolor sit amet</h4><div class="thumb" style="background:linear-gradient(135deg,#d7b48a,#6f4a2e)" role="img" aria-label="Person using a tablet at home"></div><p>Sed ut perspiciatis unde omnis iste natus error sit voluptatem accusantium doloremque.</p></article>
<article class="abs blog" style="left:600px"><div class="date">Oct 10, 2018</div><h4>Lorem ipsum dolor sit amet</h4><div class="thumb" style="background:linear-gradient(135deg,#f1c25b,#b0522a)" role="img" aria-label="Smart home illustration with connected devices"></div><p>Sed ut perspiciatis unde omnis iste natus error sit voluptatem accusantium doloremque.</p></article>
<article class="abs blog" style="left:840px"><div class="date">Oct 10, 2018</div><h4>Lorem ipsum dolor sit amet</h4><div class="thumb" style="background:linear-gradient(135deg,#3e6fa8,#0f2240)" role="img" aria-label="Connected city network at night"></div><p>Sed ut perspiciatis unde omnis iste natus error sit voluptatem accusantium doloremque.</p></article>

<p class="abs quote">Lorem ipsum dolor sit amet, consectetur adipiscing elit, sed do eiusmod tempor incididunt ut labore et dolore magna aliqua.</p>
<p class="abs byline">Posted 7 hours ago | @Dana Orell</p>

<footer class="abs footer">
  <div class="col" style="width:392px;padding-left:20px;padding-right:40px">
    <h5>About the Our Clever Dwelling</h5>
    <p>Lorem ipsum dolor sit amet, consectetur adipiscing elit, sed do eiusmod tempor incididunt ut labore et dolore magna aliqua.</p>
  </div>
  <div class="col" style="width:280px">
    <h5>Follow Us Out There</h5>
    <div class="foot-social"><span></span><span></span><span></span></div>
  </div>
  <div class="col" style="width:288px">
    <h5>Newsletter</h5>
    <div class="signup"><div class="field">Email Address</div><div class="btn">Submit</div></div>
  </div>
</footer>

<div class="abs bottombar">
  <div class="links"><span>Home</span><span>Product</span><span>FAQs</span><span>About Us</span><span>Support</span><span>Blog Posts</span><span>Contact Us</span></div>
  <div class="copy">© 2018 Copyrights | All Rights Reserved | Returns Policy</div>
  <div class="cur">EUR</div>
</div>
</body>
</html>
```